Design a New Business Card for Our Company

We are looking for fresh, unique, and a modern business card that reflects our roots as digital marketing agency focused on SEM.

Industry/Entity Type

Marketing

Contact Information for Business Card

looking for very unique out of the box designs. clean and modern that compliments our logo

Requirements
Must have
• colors should match our logo
• Front should have name, address, email, and phone/fax of the person, phone/fax are the same number
• back should have our url

```html
<!DOCTYPE html>
<html lang="en">
<head>
<meta charset="utf-8">
<title>Brightwave Solutions — Business Card</title>
<link rel="stylesheet" href="https://fonts.googleapis.com/css2?family=Open+Sans:wght@400;600&display=swap">
<style>
  :root {
    --stage: #3b3b3b;
    --card-front: #ffffff;
    --card-back: #b3b3b3;
    --brand-blue: #5b93d3;
    --brand-grey: #9b9b9b;
    --ink: #555555;
    --icon: #8a8a8a;
    --white: #ffffff;
  }
  * { box-sizing: border-box; margin: 0; padding: 0; }
  html, body { width: 1105px; height: 1200px; overflow: hidden; }
  body {
    background: var(--stage);
    font-family: "Open Sans", sans-serif;
    position: relative;
  }
  .card {
    position: absolute;
    left: 196px;
    width: 720px;
    height: 412px;
  }
  .card--front { top: 146px; background: var(--card-front); }
  .card--back  { top: 602px; background: var(--card-back); }

  .accent-band {
    position: absolute; left: 0; top: 72px;
    width: 66px; height: 76px;
    background: var(--brand-blue);
  }
  .brand {
    position: absolute;
    display: flex; align-items: center; gap: 16px;
    font-weight: 600;
    white-space: nowrap;
  }
  .brand__dot { border-radius: 50%; flex: none; }
  .card--front .brand { left: 54px; top: 82px; }
  .card--front .brand__dot { width: 56px; height: 56px; background: var(--brand-blue); }
  .card--front .brand__name { font-size: 40px; color: var(--brand-grey); letter-spacing: -0.5px; }

  .person { position: absolute; left: 119px; top: 198px; }
  .person__name { font-size: 26px; color: var(--brand-grey); line-height: 1.2; }
  .person__title { font-size: 20px; color: var(--brand-blue); line-height: 1.4; }

  .contact-list {
    position: absolute; left: 119px; top: 280px;
    list-style: none; font-size: 19px; color: var(--ink);
  }
  .contact-list li { display: flex; align-items: center; height: 27.5px; }
  .contact-list svg { width: 18px; height: 18px; margin-right: 10px; fill: var(--icon); }

  .address {
    position: absolute; right: 47px; top: 308px;
    font-style: normal; text-align: right;
    font-size: 19px; color: var(--ink); line-height: 27.5px;
  }

  .card--back .brand {
    left: 50%; top: 178px; transform: translateX(-50%);
  }
  .card--back .brand__dot { width: 66px; height: 66px; background: var(--white); }
  .card--back .brand__name { font-size: 48px; color: var(--white); letter-spacing: -0.5px; }

  .website {
    position: absolute; left: 0; right: 0; top: 347px;
    text-align: center; font-size: 18px; letter-spacing: 4px;
    color: var(--white);
  }
</style>
</head>
<body>
  <section class="card card--front" aria-label="Business card front">
    <div class="accent-band"></div>
    <div class="brand">
      <span class="brand__dot"></span>
      <span class="brand__name">Brightwave Solutions</span>
    </div>

    <div class="person">
      <p class="person__name">Daniel Reyes</p>
      <p class="person__title">CEO/Founder</p>
    </div>

    <ul class="contact-list">
      <li>
        <svg viewBox="0 0 24 24" aria-hidden="true"><path d="M6.6 10.8a15.1 15.1 0 0 0 6.6 6.6l2.2-2.2c.3-.3.7-.4 1-.2 1.1.4 2.3.6 3.6.6.6 0 1 .4 1 1V20c0 .6-.4 1-1 1A17 17 0 0 1 3 4c0-.6.4-1 1-1h3.5c.6 0 1 .4 1 1 0 1.3.2 2.5.6 3.6.1.3 0 .7-.2 1z"/></svg>
        555 210 4870
      </li>
      <li>
        <svg viewBox="0 0 24 24" aria-hidden="true"><path d="M6 3h9l3 3v4H6z M3 11h18v7h-3v3H6v-3H3z M8 16v3h8v-3z"/></svg>
        555 210 4871
      </li>
      <li>
        <svg viewBox="0 0 24 24" aria-hidden="true"><path d="M2 5h20v14H2z M4 7v.5l8 5 8-5V7l-8 5z" fill-rule="evenodd"/></svg>
        daniel@brightwavemail.com
      </li>
    </ul>

    <address class="address">
      4120 Alder Court<br>
      Fairview, Oregon 97024
    </address>
  </section>

  <section class="card card--back" aria-label="Business card back">
    <div class="brand">
      <span class="brand__dot"></span>
      <span class="brand__name">Brightwave Solutions</span>
    </div>
    <p class="website">www.brightwave-sem.com</p>
  </section>
</body>
</html>
```